Consultancy Business Card Design

We need a business card design for a new company based in singapore called KestrelOak. KestrelOak a boutique consultancy firm offering broad-based business solutions, from conception to re-invention, for ventures from new start-ups to long-running traditional businesses.
Its 2 main divisions (Food & Beverage Operations and Construction & Project Management) have access to a wide range of networks, knowledge bases, and resources to service its clients across numerous diverse sectors. This includes, and is not limited to, construction, F&B, and retail.
We are a company that combines the ambition, boldness and energy of one in the 20s with the dedication, level-headedness and dependability of one entering its 30s. Bridging the experiences of the old with ideals of the young, we draw on the positives of both to create a unique synergy.
We hope to see designs that fits our company profile.
Industry/Entity Type
Boutique
Contact Information for Business Card
KestrelOak(Company Name)
Marcus Thiel (Name)
Principle Consultant (Title)
F&B and Hospitality (Division)
(+65) 8043 5617 (Contact no.)
marcus@kestreloak.com.sg (Email)
Colors
Designer to choose colors to be used in the design.

```html
<!DOCTYPE html>
<html lang="en">
<head>
<meta charset="utf-8">
<title>KestrelOak Business Card</title>
<link rel="stylesheet" href="https://fonts.googleapis.com/css2?family=Montserrat:wght@400;500;600&display=swap">
<style>
  :root {
    --bg: #1c1c1e;
    --card-top: #2a2a2c;
    --card-bottom: #0e0e0f;
    --red: #ec2a2a;
    --red-soft: #ff4a45;
    --white: #f2f2f2;
    --grey: #cfcfcf;
  }
  * { margin: 0; padding: 0; box-sizing: border-box; }
  html, body { width: 1200px; height: 900px; overflow: hidden; }
  body {
    background: var(--bg);
    font-family: "Montserrat", sans-serif;
    display: flex;
    flex-direction: column;
    align-items: center;
    justify-content: center;
    gap: 40px;
  }
  .card {
    position: relative;
    width: 620px;
    height: 354px;
    background: radial-gradient(ellipse at 55% 40%, var(--card-top), var(--card-bottom) 80%);
    box-shadow: 0 14px 30px rgba(0,0,0,0.55);
    overflow: hidden;
  }
  .card__band {
    position: absolute;
    left: 0;
    width: 100%;
    height: 20px;
    background: linear-gradient(180deg, var(--red-soft), var(--red));
  }
  .card__band--top { top: 0; }
  .card__band--bottom { bottom: 0; }
  .wordmark {
    position: absolute;
    display: flex;
    align-items: center;
    gap: 10px;
    font-weight: 400;
    color: var(--white);
    letter-spacing: 0.5px;
  }
  .wordmark__mark {
    width: 12px;
    height: 12px;
    background: var(--red);
  }
  .card--back .wordmark { left: 200px; top: 150px; font-size: 40px; }
  .card--front .wordmark { left: 56px; top: 68px; font-size: 36px; }
  .contact-list {
    position: absolute;
    left: 310px;
    top: 170px;
    list-style: none;
    display: flex;
    flex-direction: column;
    gap: 20px;
  }
  .contact-item {
    display: flex;
    align-items: flex-start;
    gap: 16px;
    font-size: 13px;
    font-weight: 500;
    line-height: 1.3;
    color: var(--white);
  }
  .contact-item__icon {
    flex: none;
    width: 26px;
    height: 26px;
    border: 1.5px solid var(--red);
    display: flex;
    align-items: center;
    justify-content: center;
  }
  .contact-item__icon svg { width: 14px; height: 14px; fill: var(--red); }
  .contact-item__title { color: var(--red-soft); font-weight: 600; }
  .contact-item__accent { color: var(--red-soft); }
  .contact-item__muted { color: var(--grey); }
</style>
</head>
<body>
  <section class="card card--back" aria-label="Card back">
    <div class="card__band card__band--top"></div>
    <div class="wordmark"><span class="wordmark__mark"></span>KestrelOak</div>
    <div class="card__band card__band--bottom"></div>
  </section>

  <section class="card card--front" aria-label="Card front">
    <div class="card__band card__band--top"></div>
    <div class="wordmark"><span class="wordmark__mark"></span>KestrelOak</div>
    <ul class="contact-list">
      <li class="contact-item">
        <span class="contact-item__icon">
          <svg viewBox="0 0 14 14"><circle cx="7" cy="4.2" r="3"/><path d="M1.5 14c0-3.4 2.5-5.5 5.5-5.5s5.5 2.1 5.5 5.5z"/></svg>
        </span>
        <span>Marcus Thiel<br><span class="contact-item__title">Principle Consultant</span><br>F&amp;B and Hospitality</span>
      </li>
      <li class="contact-item">
        <span class="contact-item__icon">
          <svg viewBox="0 0 14 14"><path d="M3 1l2.2 2.6-1.2 1.6c.8 1.8 2.1 3.1 3.9 3.9l1.6-1.2L12.1 10l-1.3 2.3C6 12.6 1.4 8 1.7 3.2z"/></svg>
        </span>
        <span><span class="contact-item__accent">(+65)</span> 8043 5617</span>
      </li>
      <li class="contact-item">
        <span class="contact-item__icon">
          <svg viewBox="0 0 14 14"><path d="M1 3h12v8H1z M2 4l5 4 5-4" fill="none" stroke="#ec2a2a" stroke-width="1.4"/></svg>
        </span>
        <span><span class="contact-item__muted">marcus</span><span class="contact-item__accent">@kestreloak.com.sg</span></span>
      </li>
    </ul>
    <div class="card__band card__band--bottom"></div>
  </section>
</body>
</html>
```